eCommerce website for a DIY shop & communal center

We need a website for a business called The Maple Bench. The Maple Bench is both a shop and communal establishment where people with shared interests, especially in DIY (Do It Yourself) and crafting, can gather to shop for & work on projects while sharing ideas, equipment, supplies and knowledge. The shop is both brick & motor and online. The physical communal space provides workstations, equipment, tools and supplies and expertise for DIY lovers to create their projects.

Target Market(s)

Middle & upper class DIY enthusiasts, creative hobbyists, budding artists & small business owners

Industry/Entity Type

DIY, Arts & Crafts

Coding

Coded - Design and coding required

Number of Pages Required

5+ page

Requirements
Must have
• Menus to include 1. home page (with about us, operating hours, contacts, location, meet the team); 2. Bench activities (how to DIY at the Bench, booking, equipment & tools, house rules); 3. Bench events (events in the Bench, offsite events); 4. Resources (FAQs, tutorials, blogs, eBooks) and 5. Online shop
Nice to have
• Branding guidelines eg logo colours (see attachment) to influence design. Tillpost shop. Booking feature for activities & events at the Bench.

```html
<!DOCTYPE html>
<html lang="en">
<head>
<meta charset="utf-8">
<title>The Maple Bench – Online Store</title>
<link href="https://fonts.googleapis.com/css2?family=Roboto:wght@400;500;700&family=Inter:wght@400;500;600&family=Fraunces:wght@500&display=swap" rel="stylesheet">
<style>
:root{
  --ink:#111;
  --text:#222;
  --muted:#555;
  --line:#dcdcdc;
  --accent:#f4763a;
  --star:#f5b50a;
  --footer:#0a0a0a;
  --white:#fff;
}
*{box-sizing:border-box;margin:0;padding:0}
html,body{width:1200px;height:2824px;overflow:hidden;background:var(--white);font-family:"Inter",sans-serif;color:var(--text)}
.page{position:relative;width:1200px;height:2824px}
.wrap{position:absolute;left:100px;width:1000px}

/* header */
.topbar{position:absolute;top:0;left:0;width:1200px;height:49px;border-bottom:1px solid var(--line)}
.phone{position:absolute;left:100px;top:5px;display:flex;align-items:center;gap:10px;font:500 15px "Roboto",sans-serif;color:var(--ink)}
.phone .ring{width:38px;height:38px;border:1px solid #999;border-radius:50%;display:flex;align-items:center;justify-content:center}
.social-top{position:absolute;right:100px;top:5px;display:flex;gap:6px}
.social-top span{width:38px;height:38px;border:1px solid #999;border-radius:50%;display:block}
.nav{position:absolute;top:62px;left:100px;width:1001px;display:flex;justify-content:space-between;font:500 15.5px "Roboto",sans-serif;color:var(--ink)}
.nav .gap{width:195px}
.brand{position:absolute;left:525px;top:0;width:150px;height:134px;background:var(--white);border-radius:0 0 75px 75px;display:flex;align-items:center;justify-content:center;z-index:2;text-align:center}
.brand span{font:700 19px/1.15 "Roboto",sans-serif;color:var(--accent)}

/* hero */
.hero{position:absolute;top:101px;left:0;width:1200px;height:295px;background:linear-gradient(100deg,#5b4331 0%,#8a6a4c 35%,#9a3e32 55%,#4a5566 80%,#7a6a58 100%)}
.hero h1{position:absolute;left:103px;top:83px;font:700 56px "Roboto",sans-serif;color:var(--white);letter-spacing:.5px}

/* listing */
.list-head{top:477px;height:46px;display:flex;justify-content:space-between;align-items:center}
.list-head h2{font:500 32px "Fraunces",serif;color:var(--ink)}
.sort{width:176px;height:46px;border:1px solid var(--line);display:flex;align-items:center;justify-content:space-between;padding:0 12px 0 19px;font:400 17px "Roboto",sans-serif;color:#666}
.grid{top:556px;display:grid;grid-template-columns:repeat(3,320px);column-gap:20px;row-gap:40px}
.card{height:400px}
.card .photo{display:block;width:320px;height:332px}
.card .row1{display:flex;justify-content:space-between;align-items:center;margin-top:22px;padding:0 2px}
.card h3{font:500 17.5px "Inter",sans-serif;color:var(--ink)}
.card .row2{display:flex;align-items:center;gap:12px;margin-top:12px;padding-left:2px;font:400 16px "Inter",sans-serif;color:var(--ink)}
.stars{color:var(--star);font-size:13px;letter-spacing:-1px}
.reviews{font-size:11px;color:#333}

.pager{top:2341px;display:flex;justify-content:center;gap:8px;font:400 15px "Roboto",sans-serif}
.pager span{min-width:29px;height:29px;border:1px solid #ccc;display:flex;align-items:center;justify-content:center;color:#888;padding:0 12px}
.pager span.num{padding:0}
.pager .on{background:var(--accent);border-color:var(--accent);color:var(--white)}

/* footer */
.footer{position:absolute;top:2468px;left:0;width:1200px;height:356px;background:var(--footer);color:var(--white)}
.fcol{position:absolute;top:76px}
.fcol h4{font:700 17px "Roboto",sans-serif;margin-bottom:12px}
.fcol li{list-style:none;font:400 14.5px/28px "Inter",sans-serif}
.email{width:257px;height:42px;border-radius:21px;background:var(--white);color:#333;font:400 13px "Inter",sans-serif;padding:0 15px;display:flex;align-items:center}
.subscribe{width:257px;height:42px;border-radius:21px;background:var(--accent);margin-top:8px;display:flex;align-items:center;justify-content:center;font:700 14px "Roboto",sans-serif}
.fsocial{display:flex;gap:6px;margin:24px 0 0 8px}
.fsocial span{width:35px;height:35px;border-radius:50%;background:var(--white);display:block}
.rule{position:absolute;top:293px;left:100px;width:1000px;height:1px;background:#2a2a2a}
.copy{position:absolute;top:311px;width:1200px;text-align:center;font:400 13px "Inter",sans-serif}
</style>
</head>
<body>
<div class="page">
  <header>
    <div class="topbar">
      <div class="phone">
        <span class="ring"><svg width="16" height="16" viewBox="0 0 24 24" fill="none" stroke="#333" stroke-width="1.8"><path d="M22 16.9v3a2 2 0 0 1-2.2 2 19.8 19.8 0 0 1-8.6-3.1 19.5 19.5 0 0 1-6-6A19.8 19.8 0 0 1 2.1 4.2 2 2 0 0 1 4.1 2h3a2 2 0 0 1 2 1.7c.1 1 .4 1.9.7 2.8a2 2 0 0 1-.5 2.1L8 9.9a16 16 0 0 0 6 6l1.3-1.3a2 2 0 0 1 2.1-.4c.9.3 1.8.6 2.8.7a2 2 0 0 1 1.7 2z"/></svg></span>
        555 - 014 - 2290
      </div>
      <div class="social-top" aria-label="Social links"><span></span><span></span><span></span><span></span></div>
    </div>
    <div class="brand"><span>The Maple<br>Bench</span></div>
    <nav class="nav">
      <span>HOME</span><span>BENCH ACTIVITIES</span><span>BENCH EVENTS</span><span class="gap"></span><span>RESOURCES</span><span>ONLINE SHOP</span><span>CONTACT US</span>
    </nav>
  </header>

  <section class="hero" role="img" aria-label="Woman working on a woodcraft project at a workshop bench">
    <h1>ONLINE STORE</h1>
  </section>

  <div class="wrap list-head">
    <h2>Best Selling</h2>
    <div class="sort">Best Selling <svg width="12" height="8" viewBox="0 0 12 8"><path d="M1 1l5 5 5-5z" fill="#111"/></svg></div>
  </div>

  <main class="wrap grid">
    <article class="card"><div class="photo" role="img" aria-label="Pine wood shelving cabinet" style="background:linear-gradient(160deg,#c9c2b2,#d9c49a 60%,#b79c6f)"></div><div class="row1"><h3>Finibus Bonorum et Malorum</h3><svg width="20" height="18" viewBox="0 0 24 22" fill="none" stroke="#111" stroke-width="1.8"><path d="M12 20s-9-5.6-9-12a5 5 0 0 1 9-3 5 5 0 0 1 9 3c0 6.4-9 12-9 12z"/></svg></div><div class="row2">From $40.00 <span class="stars">★★★★★</span><span class="reviews">(200+reviewer)</span></div></article>
    <article class="card"><div class="photo" role="img" aria-label="Acrylic seascape painting with a boat on an easel" style="background:linear-gradient(160deg,#cbb89a,#3a6fd0 45%,#2d5bb8 75%,#c7b08a)"></div><div class="row1"><h3>Finibus Bonorum et Malorum</h3><svg width="20" height="18" viewBox="0 0 24 22" fill="none" stroke="#111" stroke-width="1.8"><path d="M12 20s-9-5.6-9-12a5 5 0 0 1 9-3 5 5 0 0 1 9 3c0 6.4-9 12-9 12z"/></svg></div><div class="row2">From $40.00 <span class="stars">★★★★★</span><span class="reviews">(200+reviewer)</span></div></article>
    <article class="card"><div class="photo" role="img" aria-label="Sunset painted on a wood slice" style="background:radial-gradient(circle at 50% 55%,#f6c141,#e9833a 35%,#3c79c9 55%,#1d2128 75%)"></div><div class="row1"><h3>Finibus Bonorum et Malorum</h3><svg width="20" height="18" viewBox="0 0 24 22" fill="none" stroke="#111" stroke-width="1.8"><path d="M12 20s-9-5.6-9-12a5 5 0 0 1 9-3 5 5 0 0 1 9 3c0 6.4-9 12-9 12z"/></svg></div><div class="row2">From $40.00 <span class="stars">★★★★★</span><span class="reviews">(200+reviewer)</span></div></article>

    <article class="card"><div class="photo" role="img" aria-label="Wooden dartboard cabinet outdoors" style="background:linear-gradient(160deg,#3c4a36,#e3cfc0 40%,#d8c2b0 65%,#8a3a2e)"></div><div class="row1"><h3>Finibus Bonorum et Malorum</h3><svg width="20" height="18" viewBox="0 0 24 22" fill="none" stroke="#111" stroke-width="1.8"><path d="M12 20s-9-5.6-9-12a5 5 0 0 1 9-3 5 5 0 0 1 9 3c0 6.4-9 12-9 12z"/></svg></div><div class="row2">From $40.00 <span class="stars">★★★★★</span><span class="reviews">(200+reviewer)</span></div></article>
    <article class="card"><div class="photo" role="img" aria-label="Stacked wooden tower lamps glowing" style="background:linear-gradient(90deg,#3a1d0c,#e0862e 30%,#5a2c10 50%,#f09a3a 75%,#2a1508)"></div><div class="row1"><h3>Finibus Bonorum et Malorum</h3><svg width="20" height="18" viewBox="0 0 24 22" fill="none" stroke="#111" stroke-width="1.8"><path d="M12 20s-9-5.6-9-12a5 5 0 0 1 9-3 5 5 0 0 1 9 3c0 6.4-9 12-9 12z"/></svg></div><div class="row2">From $40.00 <span class="stars">★★★★★</span><span class="reviews">(200+reviewer)</span></div></article>
    <article class="card"><div class="photo" role="img" aria-label="Hanging resin art tiles on driftwood" style="background:linear-gradient(160deg,#e6e1d4,#dcd6c8 60%,#cfc8b8)"></div><div class="row1"><h3>Finibus Bonorum et Malorum</h3><svg width="20" height="18" viewBox="0 0 24 22" fill="none" stroke="#111" stroke-width="1.8"><path d="M12 20s-9-5.6-9-12a5 5 0 0 1 9-3 5 5 0 0 1 9 3c0 6.4-9 12-9 12z"/></svg></div><div class="row2">From $40.00 <span class="stars">★★★★★</span><span class="reviews">(200+reviewer)</span></div></article>

    <article class="card"><div class="photo" role="img" aria-label="Blue slatted wooden plant stand with climbing plant" style="background:linear-gradient(100deg,#f0f1f0,#4f6e8f 40%,#3c5a78 60%,#e9ebea)"></div><div class="row1"><h3>Finibus Bonorum et Malorum</h3><svg width="20" height="18" viewBox="0 0 24 22" fill="none" stroke="#111" stroke-width="1.8"><path d="M12 20s-9-5.6-9-12a5 5 0 0 1 9-3 5 5 0 0 1 9 3c0 6.4-9 12-9 12z"/></svg></div><div class="row2">From $40.00 <span class="stars">★★★★★</span><span class="reviews">(200+reviewer)</span></div></article>
    <article class="card"><div class="photo" role="img" aria-label="Framed basketball jersey" style="background:linear-gradient(160deg,#4a5a3a,#e8e8e6 30%,#1c2024 55%,#e8e8e6 80%,#56603f)"></div><div class="row1"><h3>Finibus Bonorum et Malorum</h3><svg width="20" height="18" viewBox="0 0 24 22" fill="none" stroke="#111" stroke-width="1.8"><path d="M12 20s-9-5.6-9-12a5 5 0 0 1 9-3 5 5 0 0 1 9 3c0 6.4-9 12-9 12z"/></svg></div><div class="row2">From $40.00 <span class="stars">★★★★★</span><span class="reviews">(200+reviewer)</span></div></article>
    <article class="card"><div class="photo" role="img" aria-label="Wooden chicken coop with straw" style="background:linear-gradient(160deg,#6b6a62,#d6a35a 35%,#c99a5e 65%,#8a6a48)"></div><div class="row1"><h3>Finibus Bonorum et Malorum</h3><svg width="20" height="18" viewBox="0 0 24 22" fill="none" stroke="#111" stroke-width="1.8"><path d="M12 20s-9-5.6-9-12a5 5 0 0 1 9-3 5 5 0 0 1 9 3c0 6.4-9 12-9 12z"/></svg></div><div class="row2">From $40.00 <span class="stars">★★★★★</span><span class="reviews">(200+reviewer)</span></div></article>

    <article class="card"><div class="photo" role="img" aria-label="Wooden toy play kitchen" style="background:linear-gradient(160deg,#5a4a3a,#e6d2ae 35%,#efe6d6 65%,#8a3a2e)"></div><div class="row1"><h3>Finibus Bonorum et Malorum</h3><svg width="20" height="18" viewBox="0 0 24 22" fill="none" stroke="#111" stroke-width="1.8"><path d="M12 20s-9-5.6-9-12a5 5 0 0 1 9-3 5 5 0 0 1 9 3c0 6.4-9 12-9 12z"/></svg></div><div class="row2">From $40.00 <span class="stars">★★★★★</span><span class="reviews">(200+reviewer)</span></div></article>
    <article class="card"><div class="photo" role="img" aria-label="Wooden dining table with benches in a garden" style="background:linear-gradient(180deg,#6c7a5a,#d8cdb4 50%,#a99d86)"></div><div class="row1"><h3>Finibus Bonorum et Malorum</h3><svg width="20" height="18" viewBox="0 0 24 22" fill="none" stroke="#111" stroke-width="1.8"><path d="M12 20s-9-5.6-9-12a5 5 0 0 1 9-3 5 5 0 0 1 9 3c0 6.4-9 12-9 12z"/></svg></div><div class="row2">From $40.00 <span class="stars">★★★★★</span><span class="reviews">(200+reviewer)</span></div></article>
    <article class="card"><div class="photo" role="img" aria-label="Slatted wooden crate held outdoors" style="background:linear-gradient(160deg,#5c4a36,#dccdb0 45%,#8a4a32 80%)"></div><div class="row1"><h3>Finibus Bonorum et Malorum</h3><svg width="20" height="18" viewBox="0 0 24 22" fill="none" stroke="#111" stroke-width="1.8"><path d="M12 20s-9-5.6-9-12a5 5 0 0 1 9-3 5 5 0 0 1 9 3c0 6.4-9 12-9 12z"/></svg></div><div class="row2">From $40.00 <span class="stars">★★★★★</span><span class="reviews">(200+reviewer)</span></div></article>
  </main>

  <div class="wrap pager">
    <span class="num on">1</span><span class="num">2</span><span class="num">3</span><span>Next</span>
  </div>

  <footer class="footer">
    <div class="fcol" style="left:101px"><h4>ABOUT</h4><ul><li>Our Story</li><li>Press</li><li>Locations</li><li>Blog</li><li>Contact Us</li></ul></div>
    <div class="fcol" style="left:236px"><h4>OUR OFFERING</h4><ul><li>Projects</li><li>Paint Room™</li><li>Parties</li><li>Classes</li></ul></div>
    <div class="fcol" style="left:421px"><h4>OTHER</h4><ul><li>Franchise</li><li>Gift Cards</li><li>FAQ</li><li>Refund Policy</li></ul></div>
    <div class="fcol" style="left:571px"><h4>CONTACT US</h4><ul><li>48 Alder Lane Riverton USA</li><li>30417</li><li>555 - 014 - 2290</li><li>info@maplebench.com</li></ul></div>
    <div class="fcol" style="left:842px"><h4>GET UPDATES &amp; PROMOS</h4>
      <div class="email">Email Address</div>
      <div class="subscribe">SUBSCRIBE</div>
      <div class="fsocial" aria-label="Social links"><span></span><span></span><span></span><span></span></div>
    </div>
    <div class="rule"></div>
    <p class="copy">Copyright © 2021 The Maple Bench. All rights reserved.</p>
  </footer>
</div>
</body>
</html>
```